Fastest Work at home Solution for Small Businesses

We need a web page for a product called *BrightReed*
We develop an innovative VPN Appliance (Model-Name ->Reed Alpha) that gives small business the possibility literally setup the possibility for Companies to let their employees work from home.
With our secure appliance we create safe connection between any business and the employee *working at home*
Our Products *Reed Alpha* are rolled out in minutes.
A. Employees can connect directly
B. Work from any location
C. All this without having to change the company firewall
Use case
=======
1. Go to our page
2. Select Product
3. Order
4. Connect to any Switch in the company
5. install software on employees laptop
***** INSTANT Connection ******
Target Market(s)
Businesses
Coding
Coded - Design and coding required
Number of Pages Required
3 page
Font styles to use
Look and feel
Each slider illustrates characteristics of the customer's brand and the style your logo design should communicate.

```html
<!DOCTYPE html>
<html lang="en">
<head>
<meta charset="utf-8">
<title>BrightReed – Fastest Work at Home Solution for Small Businesses</title>
<link rel="stylesheet" href="https://fonts.googleapis.com/css2?family=IBM+Plex+Sans:wght@400;500;600;700&family=Poppins:wght@800&display=swap">
<style>
:root{
  --navy:#0c1a3d;
  --royal:#0d2ca8;
  --sky:#45c2f5;
  --sky-soft:#e9f1fb;
  --grey-band:#efedee;
  --line:#bdbdbd;
  --text:#2a2f3a;
  --footer:#0b1a47;
  --white:#ffffff;
}
*{box-sizing:border-box;margin:0;padding:0}
html,body{width:1200px;height:3177px;overflow:hidden}
body{position:relative;background:var(--white);font-family:"IBM Plex Sans",sans-serif;color:var(--navy)}
.abs{position:absolute}
/* header */
.site-header{position:absolute;left:0;top:0;width:1200px;height:76px;background:var(--white)}
.brand{position:absolute;left:132px;top:18px;display:flex;align-items:center;gap:10px;font-weight:700;font-size:34px;color:var(--navy);letter-spacing:-.5px}
.brand-dot{width:30px;height:30px;border-radius:50%;background:var(--royal)}
.nav a{position:absolute;top:33px;font-size:14.5px;font-weight:500;color:var(--navy);text-decoration:none;letter-spacing:.2px}
.nav a.active{color:var(--sky);text-decoration:underline;text-underline-offset:3px}
/* hero */
.hero-photo{position:absolute;left:0;top:76px;width:1200px;height:590px;background:linear-gradient(110deg,#dfe6e9 0%,#b9c4c8 35%,#8f8378 60%,#c9c1b6 100%)}
.hero-card{position:absolute;left:117px;top:203px;width:401px;height:179px;background:rgba(255,255,255,.88)}
.hero-card h1{position:absolute;left:28px;top:22px;font-family:"Poppins",sans-serif;font-weight:800;font-size:33px;line-height:41px;color:var(--navy);letter-spacing:-.3px}
.slider-dots{position:absolute;top:627px;left:556px;display:flex;gap:11px;align-items:center}
.slider-dots span{width:8px;height:8px;border-radius:50%;background:var(--white)}
.slider-dots span.on{width:12px;height:12px;border:2px solid var(--white);background:var(--sky)}
/* section headings */
.section-title{position:absolute;left:0;width:1200px;text-align:center;font-weight:700;font-size:23px;letter-spacing:.3px;color:var(--navy)}
.divider{position:absolute;left:567px;width:66px;height:10px}
/* product cards */
.product-card{position:absolute;top:801px;width:299px;height:395px;border:2px solid var(--sky);background:var(--white)}
.product-photo{position:absolute;left:-2px;top:-2px;width:299px;height:194px}
.product-icon{position:absolute;left:108px;top:153px;width:82px;height:82px;border-radius:50%;background:var(--sky);display:flex;align-items:center;justify-content:center}
.product-card h3{position:absolute;left:0;top:253px;width:100%;text-align:center;font-size:14px;font-weight:600;line-height:19px;color:var(--navy)}
.product-card p{position:absolute;left:30px;top:306px;width:235px;text-align:center;font-size:12.5px;line-height:18.5px;color:var(--text)}
.btn-small{position:absolute;left:101px;bottom:-16px;width:94px;height:28px;background:var(--sky);color:var(--white);font-size:12.5px;font-weight:500;display:flex;align-items:center;justify-content:center}
/* how it works */
.how-band{position:absolute;left:0;top:1277px;width:1200px;height:626px;background:var(--grey-band)}
.step-label{position:absolute;text-align:center;font-size:14px;font-weight:600;line-height:19px;color:var(--navy);width:220px}
/* why */
.feature-icon{position:absolute;width:74px;height:74px;border-radius:50%;background:var(--royal);display:flex;align-items:center;justify-content:center}
.feature h4{font-size:14.5px;font-weight:600;line-height:19px;color:var(--navy);margin-bottom:10px}
.feature p{font-size:12.5px;line-height:18.5px;color:var(--text)}
.feature{position:absolute;width:220px}
.rule{position:absolute;height:1px;background:#d6d6d6;width:298px;top:2210px}
.brand-disc{position:absolute;left:474px;top:2076px;width:246px;height:246px;border-radius:50%;background:var(--sky-soft);display:flex;align-items:center;justify-content:center;font-weight:700;font-size:28px;color:var(--royal)}
/* anywhere */
.anywhere-photo{position:absolute;left:0;top:2400px;width:600px;height:436px;background:linear-gradient(135deg,#5d5550 0%,#9a8f86 40%,#3f3b3a 100%)}
.anywhere-panel{position:absolute;left:600px;top:2400px;width:600px;height:436px;background:var(--sky)}
.anywhere-panel h2{position:absolute;left:43px;top:66px;font-size:23px;font-weight:700;color:var(--white)}
.anywhere-panel p{position:absolute;left:43px;top:114px;width:440px;font-size:17.5px;line-height:25.6px;color:var(--white)}
.btn-solid{position:absolute;left:46px;top:331px;width:125px;height:37px;background:var(--royal);color:var(--white);font-size:16px;font-weight:500;display:flex;align-items:center;justify-content:center}
/* footer */
.site-footer{position:absolute;left:0;top:2836px;width:1200px;height:341px;background:var(--footer);color:var(--white)}
.footer-brand{position:absolute;left:132px;top:98px;display:flex;align-items:center;gap:14px;font-weight:600;font-size:46px;color:var(--white)}
.footer-brand span.mark{width:40px;height:40px;border-radius:50%;background:var(--sky)}
.footer-col h5{position:absolute;top:46px;font-size:13px;font-weight:700;letter-spacing:.4px}
.footer-menu{position:absolute;left:511px;top:82px;list-style:none}
.footer-menu li{font-size:12px;line-height:19.8px}
.contact-row{position:absolute;display:flex;align-items:center;gap:10px;font-size:12px;line-height:16px}
.round-ico{width:23px;height:23px;border-radius:50%;background:var(--white);display:flex;align-items:center;justify-content:center;flex:none}
.footer-rule{position:absolute;left:132px;top:261px;width:935px;height:1px;background:#233366}
.copyright{position:absolute;left:0;top:295px;width:1200px;text-align:center;font-size:12px}
</style>
</head>
<body>

<header class="site-header">
  <div class="brand"><span class="brand-dot"></span>BrightReed</div>
  <nav class="nav">
    <a class="active" href="#" style="left:466px">HOME</a>
    <a href="#" style="left:549px">ABOUT US</a>
    <a href="#" style="left:658px">SERVICES</a>
    <a href="#" style="left:760px">HOW IT WORKS</a>
    <a href="#" style="left:896px">PRODUCTS</a>
    <a href="#" style="left:1004px">CONTACT</a>
  </nav>
</header>

<section>
  <div class="hero-photo" role="img" aria-label="Smiling man in a checked shirt working on a tablet at a home desk"></div>
  <div class="hero-card"><h1>FASTEST WORK AT<br>HOME SOLUTION FOR<br>SMALL BUSINESSES</h1></div>
  <div class="slider-dots"><span></span><span></span><span class="on"></span><span></span><span></span></div>
</section>

<section>
  <h2 class="section-title" style="top:710px">OUR PRODUCTS</h2>
  <svg class="divider" style="top:757px" viewBox="0 0 66 10"><line x1="5" y1="5" x2="61" y2="5" stroke="#45c2f5" stroke-width="2"/><circle cx="5" cy="5" r="5" fill="#45c2f5"/><circle cx="61" cy="5" r="5" fill="#45c2f5"/></svg>

  <article class="product-card" style="left:132px">
    <div class="product-photo" role="img" aria-label="Businessman in a suit working on a laptop in an office" style="background:linear-gradient(135deg,#cfd6da,#8a939a 60%,#e4e8ea)"></div>
    <div class="product-icon"><svg width="40" height="40" viewBox="0 0 40 40" fill="none" stroke="#fff" stroke-width="4" stroke-linecap="round"><path d="M17 23l6-6"/><path d="M15 19l-5 5a5 5 0 0 0 7 7l5-5"/><path d="M25 21l5-5a5 5 0 0 0-7-7l-5 5"/></svg></div>
    <h3>EMPLOYEES CAN<br>CONNECT DIRECTLY</h3>
    <p>Sed ut perspiciatis unde omnis iste natus error sit voluptatem accusanti um doloremque laudantium</p>
    <div class="btn-small">READ MORE</div>
  </article>

  <article class="product-card" style="left:451px">
    <div class="product-photo" role="img" aria-label="Smiling woman working on a laptop at home" style="background:linear-gradient(135deg,#eeeeec,#b9aea8 55%,#d8d5d2)"></div>
    <div class="product-icon"><svg width="40" height="40" viewBox="0 0 40 40" fill="#fff"><circle cx="20" cy="12" r="6"/><path d="M9 28c0-7 5-10 11-10s11 3 11 10z"/><rect x="11" y="24" width="18" height="9" rx="1" fill="#45c2f5" stroke="#fff" stroke-width="2"/></svg></div>
    <h3>WORK FROM<br>ANY LOCATION</h3>
    <p>Sed ut perspiciatis unde omnis iste natus error sit voluptatem accusanti um doloremque laudantium</p>
    <div class="btn-small">READ MORE</div>
  </article>

  <article class="product-card" style="left:767px">
    <div class="product-photo" role="img" aria-label="Digital security illustration with a shield over a city skyline" style="background:linear-gradient(180deg,#6f9fd6,#2e5f9e 70%,#1d3f6e)"></div>
    <div class="product-icon"><svg width="40" height="40" viewBox="0 0 40 40"><path d="M20 5l12 5v9c0 8-6 13-12 16-6-3-12-8-12-16v-9z" fill="#fff"/><path d="M14 20l5 5 8-9" fill="none" stroke="#45c2f5" stroke-width="3.5" stroke-linecap="round" stroke-linejoin="round"/></svg></div>
    <h3>ALL THIS WITHOUT HAVING TO<br>CHANGE THE COMPANY FIREWALL</h3>
    <p>Sed ut perspiciatis unde omnis iste natus error sit voluptatem accusanti um doloremque laudantium</p>
    <div class="btn-small">READ MORE</div>
  </article>
</section>

<section class="how-band">
  <h2 class="section-title" style="top:40px">HOW A VPN WORKS</h2>
  <svg class="divider" style="top:87px" viewBox="0 0 66 10"><line x1="5" y1="5" x2="61" y2="5" stroke="#45c2f5" stroke-width="2"/><circle cx="5" cy="5" r="5" fill="#45c2f5"/><circle cx="61" cy="5" r="5" fill="#45c2f5"/></svg>

  <svg class="abs" style="left:0;top:0" width="1200" height="626" viewBox="0 0 1200 626" fill="none" stroke="#bdbdbd" stroke-width="2.5">
    <g><rect x="175" y="183" width="192" height="192" rx="34" transform="rotate(45 271 279)"/></g>
    <g><rect x="500" y="183" width="192" height="192" rx="34" transform="rotate(45 596 279)"/></g>
    <g><rect x="825" y="183" width="192" height="192" rx="34" transform="rotate(45 921 279)"/></g>
    <g><rect x="337" y="345" width="192" height="192" rx="34" transform="rotate(45 433 441)"/></g>
    <g><rect x="662" y="345" width="192" height="192" rx="34" transform="rotate(45 758 441)"/></g>
    <g stroke="#a8a8a8" stroke-width="2">
      <path d="M345 355l25 12m0 0l-10 -2m10 2l-3 -10"/>
      <path d="M512 363l18-18m0 0h-12m12 0v12"/>
      <path d="M670 355l25 12m0 0l-10 -2m10 2l-3 -10"/>
      <path d="M837 363l18-18m0 0h-12m12 0v12"/>
    </g>
  </svg>

  <svg class="abs" style="left:237px;top:210px" width="56" height="56" viewBox="0 0 56 56"><path d="M52 4L4 26l20 6 6 20z" fill="#0d2ca8"/></svg>
  <div class="step-label" style="left:161px;top:287px">GO TO OUR PAGE</div>

  <svg class="abs" style="left:563px;top:210px" width="58" height="58" viewBox="0 0 58 58" fill="none" stroke="#0d2ca8" stroke-width="3.5"><path d="M20 4h20l12 12v38H20z"/><path d="M27 22h18M27 30h18M27 38h12"/><path d="M4 28h6l4 14h16M14 36h16" stroke-linecap="round"/><circle cx="16" cy="48" r="3" fill="#0d2ca8"/><circle cx="27" cy="48" r="3" fill="#0d2ca8"/></svg>
  <div class="step-label" style="left:486px;top:287px">ORDER</div>

  <svg class="abs" style="left:891px;top:206px" width="60" height="60" viewBox="0 0 60 60"><rect x="4" y="22" width="52" height="30" fill="#0d2ca8"/><rect x="0" y="52" width="60" height="5" fill="#0d2ca8"/><circle cx="30" cy="16" r="12" fill="#fff" stroke="#0d2ca8" stroke-width="4"/><circle cx="30" cy="16" r="3" fill="#0d2ca8"/><path d="M30 28v14m-6-6l6 6 6-6" stroke="#fff" stroke-width="4" fill="none"/></svg>
  <div class="step-label" style="left:814px;top:287px">INSTALL SOFTWARE ON<br>EMPLOYEES LAPTOP</div>

  <svg class="abs" style="left:405px;top:380px" width="58" height="52" viewBox="0 0 58 52" fill="none" stroke="#0d2ca8" stroke-width="3.5"><rect x="3" y="12" width="50" height="36" rx="3"/><path d="M18 12V4h20v8"/><path d="M34 28l16 6-7 2-2 7z" fill="#0d2ca8"/></svg>
  <div class="step-label" style="left:323px;top:463px">SELECT PRODUCT</div>

  <svg class="abs" style="left:720px;top:374px" width="70" height="64" viewBox="0 0 70 64" stroke="#0d2ca8" stroke-width="4"><path d="M35 6v24L10 52M35 30l25 22"/><circle cx="35" cy="6" r="6" fill="#0d2ca8"/><circle cx="35" cy="32" r="10" fill="#0d2ca8"/><circle cx="10" cy="54" r="8" fill="#0d2ca8"/><circle cx="60" cy="54" r="8" fill="#0d2ca8"/></svg>
  <div class="step-label" style="left:648px;top:463px">CONNECT TO ANY SWITCH<br>IN THE COMPANY</div>
</section>

<section>
  <h2 class="section-title" style="top:1951px">WHY USE BRIGHTREED</h2>
  <svg class="divider" style="top:2006px" viewBox="0 0 66 10"><line x1="5" y1="5" x2="61" y2="5" stroke="#45c2f5" stroke-width="2"/><circle cx="5" cy="5" r="5" fill="#45c2f5"/><circle cx="61" cy="5" r="5" fill="#45c2f5"/></svg>

  <div class="feature-icon" style="left:132px;top:2073px"><svg width="36" height="36" viewBox="0 0 36 36" fill="none" stroke="#fff" stroke-width="3.5"><rect x="3" y="5" width="30" height="20" rx="2"/><path d="M18 25v6M11 32h14"/></svg></div>
  <div class="feature" style="left:226px;top:2070px"><h4>USE ON 5 DEVICES<br>SIMULTANEOUSLY</h4><p>Sed ut perspiciatis unde omnis iste natus error sit voluptatem accusanti um doloremque laudantium</p></div>
  <div class="rule" style="left:131px"></div>
  <div class="feature-icon" style="left:132px;top:2248px"><svg width="36" height="36" viewBox="0 0 36 36" fill="none" stroke="#fff" stroke-width="3"><rect x="8" y="4" width="22" height="28" rx="2"/><path d="M4 8v26h22"/><path d="M13 11h12M13 17h12M13 23h12"/></svg></div>
  <div class="feature" style="left:226px;top:2246px"><h4>CONTENT FROM ANYWHERE</h4><p>Sed ut perspiciatis unde omnis iste natus error sit voluptatem accusanti um doloremque laudantium</p></div>

  <div class="brand-disc">BrightReed</div>

  <div class="feature" style="left:758px;top:2070px"><h4>UNLIMITED<br>BANDWIDTH</h4><p>Sed ut perspiciatis unde omnis iste natus error sit voluptatem accusanti um doloremque laudantium</p></div>
  <div class="feature-icon" style="left:991px;top:2073px"><svg width="40" height="36" viewBox="0 0 40 36" fill="none" stroke="#fff" stroke-width="3.5"><path d="M4 28a16 16 0 1 1 32 0z"/><path d="M20 26l7-10" stroke-linecap="round"/><path d="M10 22h3M27 22h3M20 11v3" stroke-linecap="round"/></svg></div>
  <div class="rule" style="left:758px"></div>
  <div class="feature" style="left:758px;top:2246px"><h4>24 HOUR LIVE CHAT SUPPORT</h4><p>Sed ut perspiciatis unde omnis iste natus error sit voluptatem accusanti um doloremque laudantium</p></div>
  <div class="feature-icon" style="left:991px;top:2248px"><svg width="38" height="38" viewBox="0 0 38 38" fill="none" stroke="#fff" stroke-width="3.5"><path d="M6 24v-5a13 13 0 0 1 26 0v5"/><rect x="5" y="22" width="7" height="11" rx="2"/><rect x="26" y="22" width="7" height="11" rx="2"/></svg></div>
</section>

<section>
  <div class="anywhere-photo" role="img" aria-label="Woman working on a laptop by a window with a cat on the sill"></div>
  <div class="anywhere-panel">
    <h2>WORK FROM ANYWHERE</h2>
    <p>There are many variations of passages of Lorem Ipsum available, but the majority have suffered alteration in some form, by injected humour, or randomised words which don't look even slightly believable. If you are going to use a passage of Lorem Ipsum, you need to be sure there isn't anything embarrassing hidden in the middle of text.</p>
    <div class="btn-solid">READ MORE</div>
  </div>
</section>

<footer class="site-footer">
  <div class="footer-brand"><span class="mark"></span>BrightReed</div>

  <div class="footer-col"><h5 style="left:511px">MENU</h5></div>
  <ul class="footer-menu"><li>HOME</li><li>ABOUT US</li><li>SERVICES</li><li>HOW IT WORKS</li><li>PRODUCTS</li><li>CONTACT</li></ul>

  <div class="footer-col"><h5 style="left:698px">CONTACT US</h5></div>
  <div class="contact-row" style="left:698px;top:84px"><span class="round-ico"><svg width="12" height="14" viewBox="0 0 12 14"><path d="M6 0a5 5 0 0 1 5 5c0 4-5 9-5 9S1 9 1 5a5 5 0 0 1 5-5z" fill="#0b1a47"/><circle cx="6" cy="5" r="2" fill="#fff"/></svg></span><span>2750 Harbor Lane<br>Fairview, CA 90000</span></div>
  <div class="contact-row" style="left:698px;top:136px"><span class="round-ico"><svg width="12" height="12" viewBox="0 0 12 12"><path d="M2 1l2.5 0 1 3-1.5 1a7 7 0 0 0 3 3l1-1.5 3 1V11c-6 0-10-4-10-10z" fill="#0b1a47"/></svg></span><span>Call Us<br>555.010.2040</span></div>
  <div class="contact-row" style="left:698px;top:188px"><span class="round-ico"><svg width="12" height="10" viewBox="0 0 12 10"><rect x="0" y="0" width="12" height="10" rx="1" fill="#0b1a47"/><path d="M1 1l5 4 5-4" stroke="#fff" fill="none"/></svg></span><span>E mail Us<br>hello@brightreed.example</span></div>

  <div class="footer-col"><h5 style="left:961px">FOLLOW US</h5></div>
  <div class="contact-row" style="left:961px;top:84px"><span class="round-ico"></span><span>Like us on<br>CIRCLEBOARD</span></div>
  <div class="contact-row" style="left:961px;top:134px"><span class="round-ico"></span><span>Follow us on<br>CHIRPLINE</span></div>
  <div class="contact-row" style="left:961px;top:185px"><span class="round-ico"></span><span>Follow us on<br>WORKLINK</span></div>

  <div class="footer-rule"></div>
  <p class="copyright">Copyright © 2021 All Rights Reserved</p>
</footer>

</body>
</html>
```